Wedding Ceremony Equipment Hire Business Card

I need a business card design for a new business I created called Vowline Rentals. We hire out Wedding Ceremony equipment and decorations mainly for beach and garden wedding ceremonies that include delivery, set up and dismantle. We do offer DIY Chair Hire as well.
I'd like to have a similar design and colours to our website:
www.vowlinerentals.com.au
If possible would like the front to incorporate our information and logo and the back to have two faded example pictures of our wedding ceremonies.
I have attached two photos and our logo. Please let me know if you need a better pic of our logo though.

Target Market(s)

Newly engaged couples, aged 25 and upwards

Industry/Entity Type

Wedding

Contact Information for Business Card

Vowline Rentals
Mira Holt
0412 908 146
hello@vowlinerentals.com.au
www.vowlinesocial.com/VowlineRentals

```html
<!DOCTYPE html>
<html lang="en">
<head>
<meta charset="utf-8">
<title>Vowline Rentals – Business Card</title>
<link rel="stylesheet" href="https://fonts.googleapis.com/css2?family=Cormorant+Garamond:ital,wght@1,500;1,600&family=Italianno&display=swap">
<style>
  :root {
    --stage: #2a2b2d;
    --card-dark: #25272a;
    --mint: #a9d2c4;
    --mint-light: #c3e2d7;
    --ink: #1d2a27;
    --paper: #f4f4f2;
    --ornament-dark: #2e3134;
    --sky: #5e97d4;
    --sand: #c8a77c;
    --grass: #4d7a35;
  }
  * { box-sizing: border-box; margin: 0; padding: 0; }
  html, body { width: 1200px; height: 900px; overflow: hidden; }
  body {
    background: var(--stage);
    position: relative;
    font-family: "Cormorant Garamond", Georgia, serif;
  }
  .card {
    position: absolute;
    top: 290px;
    width: 540px;
    height: 320px;
    overflow: hidden;
    box-shadow: 0 10px 28px rgba(0,0,0,.5);
  }
  .card--front { left: 40px; background: var(--card-dark); }
  .card--back { left: 620px; background: var(--card-dark); }

  .band {
    position: absolute;
    left: 0; top: 0; width: 100%;
    background: linear-gradient(90deg, var(--mint) 0%, var(--mint-light) 55%, var(--mint) 100%);
  }
  .card--front .band { height: 80px; }
  .card--back .band { height: 74px; }

  .brand {
    position: absolute;
    font-family: "Cormorant Garamond", Georgia, serif;
    font-style: italic;
    font-weight: 600;
    font-size: 30px;
    color: var(--ink);
    white-space: nowrap;
    line-height: 1;
  }
  .card--front .brand { left: 24px; top: 24px; }
  .card--back .brand { left: 170px; top: 22px; }

  .ornament-shadow {
    position: absolute;
    left: 0; bottom: 0;
    width: 300px; height: 150px;
    background: radial-gradient(ellipse at 30% 80%, var(--ornament-dark) 0%, rgba(46,49,52,0) 70%);
  }

  .holder-name {
    position: absolute;
    left: 30px; top: 132px;
    font-family: "Italianno", cursive;
    font-size: 46px;
    color: var(--paper);
    line-height: 1;
  }

  .contact-list {
    position: absolute;
    right: 18px; top: 202px;
    list-style: none;
    text-align: right;
  }
  .contact-list li {
    display: flex;
    justify-content: flex-end;
    align-items: center;
    gap: 10px;
    height: 24px;
    font-style: italic;
    font-weight: 500;
    font-size: 16px;
    color: var(--paper);
  }
  .contact-list svg { width: 13px; height: 13px; flex: none; }

  .photo {
    position: absolute;
    top: 74px; bottom: 0;
  }
  .photo--beach {
    left: 0; width: 266px;
    background: linear-gradient(180deg, var(--sky) 0%, #9cc2e6 30%, #e9e6de 45%, var(--sand) 62%, #a98a62 100%);
    opacity: .92;
  }
  .photo--garden {
    left: 272px; right: 0;
    background: linear-gradient(180deg, #4f8fd6 0%, #9ec3e4 32%, #6f8d5a 48%, var(--grass) 70%, #3d5f2a 100%);
    opacity: .92;
  }
</style>
</head>
<body>
  <section class="card card--front" aria-label="Business card front">
    <div class="band" role="img" aria-label="Mint band with soft damask flourish pattern"></div>
    <div class="brand">Vowline Rentals</div>
    <div class="ornament-shadow" role="img" aria-label="Faint dark damask flourish decoration"></div>
    <div class="holder-name">Mira Holt</div>
    <ul class="contact-list">
      <li>0412 908 146
        <svg viewBox="0 0 13 13" aria-hidden="true"><rect x="3.5" y="0.8" width="6" height="11.4" rx="1" fill="none" stroke="#f4f4f2" stroke-width="1.2"/><line x1="5.5" y1="10.2" x2="7.5" y2="10.2" stroke="#f4f4f2"/></svg>
      </li>
      <li>hello@vowlinerentals.com.au
        <svg viewBox="0 0 13 13" aria-hidden="true"><circle cx="6.5" cy="6.5" r="5.6" fill="none" stroke="#f4f4f2" stroke-width="1.1"/><ellipse cx="6.5" cy="6.5" rx="2.5" ry="5.6" fill="none" stroke="#f4f4f2" stroke-width="0.9"/><line x1="0.9" y1="6.5" x2="12.1" y2="6.5" stroke="#f4f4f2" stroke-width="0.9"/></svg>
      </li>
      <li>www.vowlinerentals.com.au
        <svg viewBox="0 0 13 13" aria-hidden="true"><rect x="0.8" y="2.5" width="11.4" height="8" fill="#f4f4f2"/><polyline points="0.8,2.5 6.5,7 12.2,2.5" fill="none" stroke="#25272a" stroke-width="1.1"/></svg>
      </li>
      <li>www.vowlinesocial.com/VowlineRentals
        <svg viewBox="0 0 13 13" aria-hidden="true"><rect x="0.5" y="0.5" width="12" height="12" rx="1.5" fill="#f4f4f2"/></svg>
      </li>
    </ul>
  </section>

  <section class="card card--back" aria-label="Business card back">
    <div class="band" role="img" aria-label="Mint band with soft damask flourish pattern"></div>
    <div class="brand">Vowline Rentals</div>
    <div class="photo photo--beach" role="img" aria-label="Faded photo of a beach wedding aisle lined with white chairs"></div>
    <div class="photo photo--garden" role="img" aria-label="Faded photo of a garden wedding aisle with white runner and chairs by the harbour"></div>
  </section>
</body>
</html>
```